Business card for law firm

Need business card for new law firm. Think confident, authoritative, conservative, but not stuffy or old-fashioned.

Contact Information for Business Card

Content for card - logo (uploaded), plus the following:

Paul Whitcombe (larger font)
Managing Partner (larger font, but not as large as name)
Level 9, 7 Ferris Lane
Sydney NSW 2000
Main Tel 02 9364 2710
Direct Tel 02 8472 3159
Email paul@qvlegal.com.au
www.qvlegal.com.au

Letterhead design should include logo plus:
Level 9, 7 Ferris Lane
Sydney NSW 2000
Tel 02 8472 3159
www.qvlegal.com.au

```html
<!DOCTYPE html>
<html lang="en">
<head>
<meta charset="utf-8">
<title>Quayvale Lawyers – Business Card</title>
<link href="https://fonts.googleapis.com/css2?family=Roboto:wght@400;500&display=swap" rel="stylesheet">
<style>
  :root {
    --backdrop: #d1d2d4;
    --card-white: #ffffff;
    --card-black: #000000;
    --ink-light: #ffffff;
    --ink-dark: #111111;
    --brand-navy: #1b2156;
  }
  html, body {
    margin: 0;
    padding: 0;
    width: 1200px;
    height: 1200px;
    overflow: hidden;
    background: var(--backdrop);
    font-family: "Roboto", Arial, sans-serif;
  }
  .business-card {
    position: absolute;
    left: 212px;
    top: 378px;
    width: 776px;
    height: 444px;
    background: var(--card-white);
    overflow: hidden;
  }
  .diagonal-panel {
    position: absolute;
    inset: 0;
  }
  .brand {
    position: absolute;
    left: 440px;
    top: 28px;
    width: 316px;
    text-align: center;
  }
  .brand-square {
    width: 68px;
    height: 68px;
    margin: 0 auto 26px;
    background: var(--brand-navy);
  }
  .brand-name {
    font-size: 34px;
    font-weight: 400;
    color: var(--ink-dark);
    letter-spacing: 1px;
    line-height: 1;
  }
  .holder {
    position: absolute;
    left: 24px;
    top: 144px;
    color: var(--ink-light);
  }
  .holder-name {
    font-size: 36px;
    font-weight: 500;
    line-height: 1.1;
    margin: 0;
  }
  .holder-title {
    font-size: 27px;
    font-weight: 400;
    margin: 6px 0 0;
  }
  .contact-row {
    position: absolute;
    display: flex;
    align-items: flex-start;
    color: var(--ink-light);
    font-size: 21px;
    line-height: 28px;
  }
  .contact-row svg {
    flex: none;
    stroke: var(--ink-light);
    fill: none;
    stroke-width: 1.4;
  }
  .row-web { left: 22px; top: 265px; gap: 15px; }
  .row-mail { left: 22px; top: 315px; gap: 14px; }
  .row-phone { left: 22px; top: 360px; gap: 22px; }
  .row-address { left: 344px; top: 360px; gap: 18px; }
  .contact-row .lines { display: flex; flex-direction: column; }
</style>
</head>
<body>
  <div class="business-card">
    <svg class="diagonal-panel" viewBox="0 0 776 444" preserveAspectRatio="none" aria-hidden="true">
      <polygon points="0,0 776,444 0,444" fill="var(--card-black)"/>
    </svg>

    <div class="brand">
      <div class="brand-square"></div>
      <div class="brand-name">Quayvale Lawyers</div>
    </div>

    <div class="holder">
      <h1 class="holder-name">Paul Whitcombe</h1>
      <p class="holder-title">Managing Partner</p>
    </div>

    <div class="contact-row row-web">
      <svg width="31" height="32" viewBox="0 0 31 32" aria-hidden="true">
        <circle cx="15" cy="15" r="13.5"/>
        <ellipse cx="15" cy="15" rx="6" ry="13.5"/>
        <line x1="1.5" y1="15" x2="28.5" y2="15"/>
        <path d="M18 18 L27 27 L23 27 L25 31 L23.5 31.6 L21.5 27.6 L19 30 Z" fill="var(--card-black)"/>
      </svg>
      <span>www.qvlegal.com.au</span>
    </div>

    <div class="contact-row row-mail">
      <svg width="30" height="22" viewBox="0 0 30 22" aria-hidden="true">
        <rect x="1" y="1" width="28" height="20"/>
        <polyline points="1,1 15,13 29,1"/>
        <line x1="1" y1="21" x2="11" y2="10"/>
        <line x1="29" y1="21" x2="19" y2="10"/>
      </svg>
      <span>paul@qvlegal.com.au</span>
    </div>

    <div class="contact-row row-phone">
      <svg width="20" height="32" viewBox="0 0 20 32" aria-hidden="true">
        <rect x="1" y="4" width="18" height="27" rx="3"/>
        <line x1="6" y1="4" x2="6" y2="1"/>
        <rect x="5" y="9" width="10" height="7"/>
        <circle cx="10" cy="25" r="1.6"/>
      </svg>
      <div class="lines">
        <span>02 9364 2710</span>
        <span>02 8472 3159</span>
      </div>
    </div>

    <div class="contact-row row-address">
      <svg width="28" height="38" viewBox="0 0 28 38" aria-hidden="true">
        <path d="M14 36 C8 27 2 21 2 14 A12 12 0 0 1 26 14 C26 21 20 27 14 36 Z"/>
        <circle cx="14" cy="14" r="4.5"/>
      </svg>
      <div class="lines">
        <span>Level 9, 7 Ferris Lane</span>
        <span>Sydney NSW 2000</span>
      </div>
    </div>
  </div>
</body>
</html>
```